Kestrelbrook Student Accomodation needs a business card design

Hi Guys,

We are a Student Accommodation company in Australia. We already have a logo which I will submit.

I will require the design of the business cards from you.

I am after something that looks clean, modern and that people feel interested and actually want to contact us.

We would like to see designs that are innovative.

On the business cards I will require to have:

Employee Name
Position
Phone number
Email
Facebook page

I hope you can help me with this project guys as I have heard really good things from you.

```html
<!DOCTYPE html>
<html lang="en">
<head>
<meta charset="utf-8">
<title>Kestrelbrook Student Accomodation – Business Card</title>
<link href="https://fonts.googleapis.com/css2?family=Montserrat:wght@400;600;800&display=swap" rel="stylesheet">
<style>
  :root {
    --green: #17961f;
    --orange: #f2a81d;
    --ink: #3a3a3a;
    --paper: #ffffff;
    --backdrop: #e7e8ea;
  }
  * { box-sizing: border-box; margin: 0; padding: 0; }
  html, body { width: 1200px; height: 988px; overflow: hidden; }
  body {
    background: var(--backdrop);
    font-family: "Montserrat", Arial, sans-serif;
    display: flex; flex-direction: column; align-items: center; justify-content: center;
    gap: 40px;
  }
  .card {
    position: relative;
    width: 760px; height: 434px;
    background: var(--paper);
    box-shadow: 0 6px 18px rgba(0,0,0,.12);
    overflow: hidden;
  }
  .band-top { position: absolute; left: 0; right: 0; top: 0; height: 12px; background: var(--green); }
  .band-bottom { position: absolute; left: 0; right: 0; bottom: 0; height: 22px; background: var(--green); }

  .brand { display: flex; align-items: center; gap: 14px; }
  .brand-mark { width: 38px; height: 38px; background: var(--green); flex: none; }
  .brand-name {
    font-weight: 800; color: var(--orange); text-transform: uppercase;
    font-size: 22px; line-height: 1.1; letter-spacing: .5px;
  }

  .card-front .brand { position: absolute; left: 50%; top: 50%; transform: translate(-50%, -50%); }

  .card-back .rule { position: absolute; left: 0; right: 0; height: 4px; background: var(--green); }
  .card-back .rule-upper { top: 58px; }
  .card-back .rule-lower { top: 370px; }
  .card-back .brand { position: absolute; left: 200px; top: 110px; }
  .card-back .brand-name { font-size: 19px; }

  .contact-list {
    position: absolute; left: 200px; top: 200px;
    list-style: none; display: grid; grid-template-columns: auto auto; gap: 14px 40px;
    font-size: 14px; color: var(--ink);
  }
  .contact-list li { display: flex; align-items: center; gap: 8px; }
  .contact-list .full { grid-column: 1 / -1; }
  .icon { width: 18px; height: 18px; flex: none; }

  .person { position: absolute; left: 48px; top: 300px; }
  .person-name { color: var(--green); font-weight: 600; font-size: 22px; letter-spacing: 1px; text-transform: uppercase; }
  .person-role { color: var(--ink); font-size: 13px; letter-spacing: 1px; text-transform: uppercase; margin-top: 4px; }
</style>
</head>
<body>

<section class="card card-front">
  <div class="band-top"></div>
  <div class="brand">
    <span class="brand-mark"></span>
    <span class="brand-name">Kestrelbrook<br>Student Accomodation</span>
  </div>
  <div class="band-bottom"></div>
</section>

<section class="card card-back">
  <div class="band-top"></div>
  <div class="rule rule-upper"></div>
  <div class="brand">
    <span class="brand-mark"></span>
    <span class="brand-name">Kestrelbrook<br>Student Accomodation</span>
  </div>
  <ul class="contact-list">
    <li>
      <svg class="icon" viewBox="0 0 18 18"><circle cx="9" cy="9" r="9" fill="var(--orange)"/><path d="M6 4.5l2 2-1 1.3c.6 1.3 1.6 2.3 2.9 2.9l1.3-1 2 2-1.3 1.5C8.6 13 5 9.4 4.5 5.8z" fill="#fff"/></svg>
      012 555 0148
    </li>
    <li>
      <svg class="icon" viewBox="0 0 18 18"><circle cx="9" cy="9" r="9" fill="var(--orange)"/><path d="M6 4.5l2 2-1 1.3c.6 1.3 1.6 2.3 2.9 2.9l1.3-1 2 2-1.3 1.5C8.6 13 5 9.4 4.5 5.8z" fill="#fff"/></svg>
      012 555 0149
    </li>
    <li>
      <svg class="icon" viewBox="0 0 18 18"><circle cx="9" cy="9" r="9" fill="var(--orange)"/><rect x="4.5" y="6" width="9" height="6.5" fill="#fff"/><path d="M4.5 6l4.5 3.5L13.5 6" stroke="var(--orange)" fill="none"/></svg>
      hello@kestrelbrook.com
    </li>
    <li>
      <svg class="icon" viewBox="0 0 18 18"><circle cx="9" cy="9" r="9" fill="var(--orange)"/><circle cx="9" cy="9" r="4.5" fill="none" stroke="#fff" stroke-width="1.3"/><path d="M4.5 9h9M9 4.5c-2 2.5-2 6.5 0 9M9 4.5c2 2.5 2 6.5 0 9" stroke="#fff" fill="none" stroke-width="1"/></svg>
      www.kestrelbrook.com
    </li>
    <li class="full">
      <svg class="icon" viewBox="0 0 18 18"><circle cx="9" cy="9" r="9" fill="var(--orange)"/><path d="M9 14s-3.5-3.8-3.5-6.2a3.5 3.5 0 017 0C12.5 10.2 9 14 9 14z" fill="#fff"/><circle cx="9" cy="7.8" r="1.3" fill="var(--orange)"/></svg>
      14 Level 3 Harbour View Road NSW
    </li>
  </ul>
  <div class="person">
    <p class="person-name">Daniel Harrow</p>
    <p class="person-role">Financial Advisor</p>
  </div>
  <div class="rule rule-lower"></div>
  <div class="band-bottom"></div>
</section>

</body>
</html>
```